Irrigation Business needs their business cards modernised and revamped

I would like to keep my current logo, colours and revamp the format of the card.

I would like the card to be clean yet important.

Im not sure if you include texture but i would like the named logo to be indented into the card etc.

show me something alive and free something thats clinical to the point yet has a feel of achievement. i would like people to go nice card.

Target Market(s)

high end clients, corporate, sports field manger, the guys that make the decisions

Industry/Entity Type

Business

Contact Information for Business Card

nformation to be included

Dean Harlow (Director)
0487305526
dean@kolvat.biz
www.kestonfieldworks.com

instagram logo
google logo
facebook logo

Colors

Designer to choose colors to be used in the design.

Requirements
Nice to have
• indentations a really nice feel to the card good texture

```html
<!DOCTYPE html>
<html lang="en">
<head>
<meta charset="utf-8">
<title>Keston Fieldworks — Business Card</title>
<link href="https://fonts.googleapis.com/css2?family=Roboto:wght@400;700;900&display=swap" rel="stylesheet">
<style>
  :root {
    --page: #3a3b3d;
    --card: #2a2b2e;
    --card-deep: #242528;
    --deboss: #1f2022;
    --blue: #3a5ca8;
    --sky: #3ea0d8;
    --green: #1e9a4c;
    --ink-light: #e6e7ea;
    --ink-muted: #b9bcc2;
    --dot-a: #c94a8e;
    --dot-b: #d9493f;
    --dot-c: #2f64b8;
  }
  * { margin: 0; padding: 0; box-sizing: border-box; }
  html, body {
    width: 799px; height: 1200px; overflow: hidden;
    background: var(--page);
    font-family: "Roboto", Arial, sans-serif;
  }
  .card {
    position: absolute; left: 70px;
    width: 660px; height: 377px;
    background: var(--card);
    border-radius: 4px;
    overflow: hidden;
    box-shadow: 0 18px 40px rgba(0,0,0,.35);
  }
  .card--front { top: 110px; }
  .card--back  { top: 713px; }
  .card svg.art { position: absolute; inset: 0; }

  /* front */
  .front-mark {
    position: absolute; left: 0; right: 0; top: 62px;
    display: flex; flex-direction: column; align-items: center; gap: 16px;
  }
  .front-mark__circle {
    width: 170px; height: 170px; border-radius: 50%;
    background: var(--deboss);
    box-shadow: inset 0 3px 6px rgba(0,0,0,.55), 0 1px 0 rgba(255,255,255,.06);
  }
  .front-mark__name {
    font-weight: 700; font-size: 20px; letter-spacing: 3px;
    color: var(--deboss);
    text-shadow: 0 1px 0 rgba(255,255,255,.07);
    text-transform: uppercase;
  }
  .social {
    position: absolute; display: flex; gap: 6px;
  }
  .social span { width: 18px; height: 18px; border-radius: 50%; display: block; }
  .social .a { background: var(--dot-a); }
  .social .b { background: var(--dot-b); }
  .social .c { background: var(--dot-c); }
  .front-social { left: 50%; transform: translateX(-50%); top: 316px; }

  /* back */
  .brand {
    position: absolute; left: 38px; top: 60px;
    display: flex; flex-direction: column; align-items: center; gap: 18px;
    width: 300px;
  }
  .brand__circle {
    width: 150px; height: 150px; border-radius: 50%;
    background: var(--blue);
  }
  .brand__name {
    font-weight: 900; font-size: 28px; color: var(--blue);
    text-transform: uppercase; letter-spacing: .5px;
  }
  .holder {
    position: absolute; right: 60px; top: 140px; text-align: right;
    color: #fff;
  }
  .holder__name { font-weight: 900; font-size: 28px; text-transform: uppercase; }
  .holder__role { font-size: 14px; color: var(--ink-light); margin-top: 4px; }

  .contact {
    position: absolute; right: 40px; top: 278px;
    text-align: right; color: var(--ink-muted); font-size: 16px; line-height: 22px;
  }
  .contact__follow { display: flex; align-items: center; justify-content: flex-end; gap: 8px; }
  .contact__follow .social { position: static; }
  .contact__row { display: flex; align-items: center; justify-content: flex-end; gap: 10px; }
  .contact__row svg { width: 14px; height: 14px; fill: var(--blue); }
</style>
</head>
<body>

<section class="card card--front" aria-label="Card front">
  <svg class="art" viewBox="0 0 660 377" aria-hidden="true">
    <line x1="150" y1="325" x2="290" y2="325" stroke="var(--blue)" stroke-width="2"/>
    <line x1="370" y1="325" x2="510" y2="325" stroke="var(--blue)" stroke-width="2"/>
  </svg>
  <div class="front-mark">
    <div class="front-mark__circle"></div>
    <div class="front-mark__name">Keston Fieldworks</div>
  </div>
  <div class="social front-social"><span class="a"></span><span class="b"></span><span class="c"></span></div>
</section>

<section class="card card--back" aria-label="Card back">
  <svg class="art" viewBox="0 0 660 377" aria-hidden="true">
    <path d="M0,0 H660 V250 C585,242 525,205 462,145 C392,78 300,42 0,30 Z" fill="var(--blue)"/>
    <path d="M60,48 C200,30 330,50 420,115" fill="none" stroke="var(--green)" stroke-width="9" stroke-linecap="round"/>
    <path d="M230,62 C340,70 410,110 470,165 C530,222 590,262 660,272" fill="none" stroke="var(--sky)" stroke-width="6"/>
  </svg>

  <div class="brand">
    <div class="brand__circle"></div>
    <div class="brand__name">Keston Fieldworks</div>
  </div>

  <div class="holder">
    <div class="holder__name">Dean Harlow</div>
    <div class="holder__role">Director</div>
  </div>

  <div class="contact">
    <div class="contact__follow">Follow us on:
      <div class="social"><span class="a"></span><span class="b"></span><span class="c"></span></div>
    </div>
    <div class="contact__row">0487305526
      <svg viewBox="0 0 16 16"><path d="M3 1h3l1.5 4-2 1.3a9 9 0 0 0 4.2 4.2L11 8.5l4 1.5v3a2 2 0 0 1-2 2A12 12 0 0 1 1 3a2 2 0 0 1 2-2z"/></svg>
    </div>
    <div class="contact__row">dean@kolvat.biz
      <svg viewBox="0 0 16 16"><path d="M1 3h14v10H1z M1 3l7 6 7-6" fill="none" stroke="var(--blue)" stroke-width="1.8"/></svg>
    </div>
    <div class="contact__row">www.kestonfieldworks.com
      <svg viewBox="0 0 16 16"><circle cx="8" cy="8" r="6.5" fill="none" stroke="var(--blue)" stroke-width="1.6"/><path d="M1.5 8h13M8 1.5c-3 3.5-3 9.5 0 13M8 1.5c3 3.5 3 9.5 0 13" fill="none" stroke="var(--blue)" stroke-width="1.2"/></svg>
    </div>
  </div>
</section>

</body>
</html>
```